Modern Business Card for Larkwell 2018

Our company assumes the best about people. We are creating an online community of entrepreneurs and business leaders who struggle with marketing their business online.

This business card should POP! We recently got a new logo and are launching a new website next month, so our business cards should make a statement that feels:
-Fresh
-Smart
-Trustworthy
-Fun

Target Market(s)

small business owners, entrepreneurs

Industry/Entity Type

Digital Marketing

Contact Information for Business Card

Dimensions: 3.5" x 2"

Font styles to use
Sans Serif

Colors
f37122
ffffff

Requirements
Must have
• We need a business card with a modern, bold design. We will use one side of the card as a lead-generation offer, so text on one side will need to fit up to 140 characters. The business card should stick to our core colors (orange, black, and white).
Nice to have
• We think a vertical "portrait" design could be interesting.
Should not have
• Should not look like a traditional business card. The round icon should stand out from a distance.

```html
<!DOCTYPE html>
<html lang="en">
<head>
<meta charset="utf-8">
<title>Larkwell Business Card</title>
<link rel="stylesheet" href="https://fonts.googleapis.com/css2?family=Roboto:wght@400;500;700&family=Roboto+Condensed:wght@700&display=swap">
<style>
  :root {
    --brand-orange: #f26a28;
    --paper: #f3f3f3;
    --ink: #222222;
    --backdrop: #e2e2e2;
    --white: #ffffff;
    --rule: #333333;
  }
  * { margin: 0; padding: 0; box-sizing: border-box; }
  html, body { width: 1200px; height: 960px; overflow: hidden; }
  body {
    position: relative;
    background: var(--backdrop);
    font-family: "Roboto", Arial, sans-serif;
    color: var(--ink);
  }
  .card {
    position: absolute;
    width: 600px;
    height: 343px;
    background: var(--paper);
    box-shadow: 0 4px 14px rgba(0,0,0,0.18);
    overflow: hidden;
  }
  .card-front { left: 302px; top: 118px; }
  .card-back { left: 299px; top: 499px; }

  /* Front */
  .holder-name {
    position: absolute; left: 53px; top: 52px;
    font-family: "Roboto Condensed", "Arial Narrow", sans-serif;
    font-weight: 700; font-size: 24px; color: var(--brand-orange);
    letter-spacing: 0.2px;
  }
  .holder-title {
    position: absolute; left: 53px; top: 80px;
    font-size: 15px; font-weight: 500; letter-spacing: 0.4px;
  }
  .front-divider {
    position: absolute; left: 295px; top: 52px;
    width: 2px; height: 44px; background: var(--brand-orange);
  }
  .holder-email {
    position: absolute; left: 326px; top: 54px;
    font-size: 15px;
  }
  .front-brand {
    position: absolute; left: 53px; top: 250px;
    display: flex; align-items: center; gap: 10px;
  }
  .brand-dot {
    width: 44px; height: 44px; border-radius: 50%;
    background: var(--brand-orange);
  }
  .front-brand .brand-name {
    font-weight: 700; font-size: 20px; color: var(--brand-orange);
    letter-spacing: 1px;
  }

  /* Back */
  .offer-band {
    position: absolute; left: 0; top: 0;
    width: 600px; height: 219px; background: var(--brand-orange);
  }
  .back-brand {
    position: absolute; left: 47px; top: 58px; width: 226px;
    display: flex; flex-direction: column; align-items: center; gap: 12px;
  }
  .back-brand .brand-dot { width: 40px; height: 40px; background: var(--white); }
  .back-brand .brand-name {
    font-weight: 700; font-size: 38px; color: var(--white);
    letter-spacing: 1.5px; line-height: 1;
  }
  .back-divider {
    position: absolute; left: 296px; top: 29px;
    width: 1px; height: 164px; background: rgba(255,255,255,0.7);
  }
  .offer {
    position: absolute; left: 322px; top: 30px; color: var(--white);
  }
  .offer-headline {
    font-weight: 700; font-size: 19px; line-height: 21px; letter-spacing: 0.2px;
  }
  .offer-copy {
    margin-top: 6px; font-size: 15px; line-height: 19.5px;
  }
  .offer-link {
    margin-top: 8px; font-weight: 700; font-size: 18px;
  }
  .note-line {
    position: absolute; left: 36px; width: 520px; height: 1px;
    background: var(--rule);
  }
  .note-line-1 { top: 260px; }
  .note-line-2 { top: 300px; }
</style>
</head>
<body>
  <section class="card card-front" aria-label="Card front">
    <div class="holder-name">NOLAN REYES</div>
    <div class="holder-title">STORY MARKETING COACH</div>
    <div class="front-divider"></div>
    <div class="holder-email">nolan@larkwellnow.com</div>
    <div class="front-brand">
      <div class="brand-dot"></div>
      <span class="brand-name">LARKWELL</span>
    </div>
  </section>

  <section class="card card-back" aria-label="Card back">
    <div class="offer-band"></div>
    <div class="back-brand">
      <div class="brand-dot"></div>
      <span class="brand-name">LARKWELL</span>
    </div>
    <div class="back-divider"></div>
    <div class="offer">
      <div class="offer-headline">REACH MORE PEOPLE.<br>MAKE MORE MONEY.<br>CREATE MORE IMPACT.</div>
      <div class="offer-copy">Get your free Larkwell<br>Starter Package and our<br>marketing guide today at</div>
      <div class="offer-link">Larkwellnow.com/start</div>
    </div>
    <div class="note-line note-line-1"></div>
    <div class="note-line note-line-2"></div>
  </section>
</body>
</html>
```